Redesign business cards

We have a new logo and I am not that happy with the layout of our existing card and looking for a change. Font is a bit small and the green can be hard to read. Logo may need a tidy up as the copy I have is not that hi-res too so require you to produce a hi-res version of the logo for us too. There will be three individual business cards to produce with just the names and phone numbers being different. Address will change too, but use what you see on the card for now.

Industry/Entity Type

Business

Requirements
Nice to have
• You could consider a redesign to the new logo, just not too radical. We like the blue and green hexagons as we feel that they are representative of oil industry that we are in.

```html
<!DOCTYPE html>
<html lang="en">
<head>
<meta charset="utf-8">
<title>Verdalis Fluid Services – Business Card</title>
<link href="https://fonts.googleapis.com/css2?family=Open+Sans:wght@400;600;700&display=swap" rel="stylesheet">
<style>
  :root {
    --bg: #e9e6e1;
    --card: #ffffff;
    --green: #8cc63e;
    --blue: #5cbfe8;
    --orange: #f39322;
    --ink: #4a4a4a;
    --muted: #8a8a8a;
    --white: #ffffff;
  }
  html, body {
    margin: 0;
    padding: 0;
    width: 1200px;
    height: 829px;
    overflow: hidden;
    background: var(--bg);
    font-family: "Open Sans", Arial, sans-serif;
  }
  .stage {
    position: relative;
    width: 1200px;
    height: 829px;
  }
  .card {
    position: absolute;
    top: 255px;
    width: 520px;
    height: 318px;
    box-sizing: border-box;
    box-shadow: 0 2px 6px rgba(0,0,0,0.12);
  }
  .card-front {
    left: 50px;
    background: var(--card);
    padding: 34px 36px;
  }
  .card-back {
    left: 630px;
    background: var(--green);
  }

  /* front */
  .brand {
    display: flex;
    align-items: center;
    gap: 10px;
    margin-top: 6px;
  }
  .brand-dot {
    width: 16px;
    height: 16px;
    border-radius: 50%;
    background: var(--blue);
  }
  .brand-name {
    font-size: 26px;
    font-weight: 700;
    color: var(--green);
    line-height: 1;
    letter-spacing: -0.3px;
  }
  .person {
    margin-top: 22px;
  }
  .person-name {
    font-size: 17px;
    font-weight: 600;
    color: var(--orange);
    margin: 0;
  }
  .person-title {
    font-size: 12px;
    color: var(--muted);
    margin: 3px 0 0;
  }
  .contacts {
    list-style: none;
    padding: 0;
    margin: 16px 0 0;
  }
  .contact {
    display: flex;
    align-items: center;
    gap: 8px;
    font-size: 13px;
    color: var(--ink);
    line-height: 23px;
  }
  .contact svg {
    width: 13px;
    height: 13px;
    flex: none;
  }
  .address {
    margin-top: 14px;
    font-size: 13px;
    line-height: 19px;
    color: var(--ink);
  }

  /* back */
  .back-brand {
    position: absolute;
    left: 0;
    right: 0;
    top: 118px;
    display: flex;
    justify-content: center;
    align-items: center;
    gap: 12px;
  }
  .back-brand .brand-dot {
    width: 20px;
    height: 20px;
    background: var(--white);
  }
  .back-brand .brand-name {
    color: var(--white);
    font-size: 30px;
  }
  .back-web {
    position: absolute;
    right: 34px;
    bottom: 30px;
    font-size: 14px;
    letter-spacing: 3px;
    color: var(--white);
  }
</style>
</head>
<body>
<main class="stage">

  <section class="card card-front" aria-label="Card front">
    <div class="brand">
      <span class="brand-dot"></span>
      <span class="brand-name">Verdalis Fluid Services</span>
    </div>

    <div class="person">
      <p class="person-name">Daniel Ashworth NZCE (Mech) P&amp;P</p>
      <p class="person-title">Director</p>
    </div>

    <ul class="contacts">
      <li class="contact">
        <svg viewBox="0 0 16 16" aria-hidden="true">
          <circle cx="8" cy="8" r="8" fill="var(--orange)"/>
          <path d="M5.2 4.2l1.5-.3.8 2-1 .7c.5 1.1 1.2 1.8 2.3 2.3l.7-1 2 .8-.3 1.5c-3.3.2-6.2-2.7-6-6z" fill="#fff"/>
        </svg>
        +61 400 318 552
      </li>
      <li class="contact">
        <svg viewBox="0 0 16 16" aria-hidden="true">
          <circle cx="8" cy="8" r="8" fill="var(--orange)"/>
          <rect x="4" y="5.2" width="8" height="5.6" fill="#fff"/>
          <path d="M4 5.2l4 3 4-3" fill="none" stroke="var(--orange)" stroke-width="0.9"/>
        </svg>
        daniel@verdalis.co.nz
      </li>
      <li class="contact">
        <svg viewBox="0 0 16 16" aria-hidden="true">
          <circle cx="8" cy="8" r="8" fill="var(--orange)"/>
          <circle cx="8" cy="8" r="4" fill="none" stroke="#fff" stroke-width="1"/>
          <path d="M4 8h8M8 4c-2 2.4-2 5.6 0 8M8 4c2 2.4 2 5.6 0 8" fill="none" stroke="#fff" stroke-width="0.8"/>
        </svg>
        www.verdalis.com.au
      </li>
    </ul>

    <p class="address">
      Verdalis Fluid Services 512 Harbour Road<br>
      PO Box 4410 | Eastbrook Queensland 4150
    </p>
  </section>

  <section class="card card-back" aria-label="Card back">
    <div class="back-brand">
      <span class="brand-dot"></span>
      <span class="brand-name">Verdalis Fluid Services</span>
    </div>
    <p class="back-web">www.verdalis.com.au</p>
  </section>

</main>
</body>
</html>
```